Promotional Ad/Flyer - Brakko Leasing

A division of our company, Brakko Leasing (brakko-leasing.example) is celebrating its 1-year anniversary in September and we would like to run a promotion. I am looking to have a promotional ad/flyer made-up for email mailings and LinkedIn posts and possibly have on our site. Have plenty of product photos to share if needed, not a prerequisite to use our product in the ad but open to it. Can also be cool graphics as well. We want to capture the viewers attention with the 30 DAYS FREE! The message is simple:
We are celebrating our 1-Year Anniversary by offering a Special Peak-Season Promotion!

FREE RENTALS for 30 days with a minimum 30-Day rental!

Valid from Sep. 1 - Dec. 31 & while supplies last.

Please contact our sales department for more details.

Email: quotes@brakko-leasing.example
Phone: +1-555-284-9317

```html
<!DOCTYPE html>
<html lang="en">
<head>
<meta charset="utf-8">
<title>Brakko Leasing – 1 Year Anniversary Promotion</title>
<link rel="stylesheet" href="https://fonts.googleapis.com/css2?family=Anton&family=Montserrat:wght@600;700&family=Tinos:ital,wght@0,400;0,700;1,700&display=swap">
<style>
  :root {
    --page-bg: #3a3a3a;
    --night: #0d0608;
    --gold-light: #fbe08a;
    --gold: #d9a520;
    --orange: #f26a0a;
    --blue: #3457b9;
    --ink: #2b2f38;
    --white: #ffffff;
  }
  * { box-sizing: border-box; margin: 0; padding: 0; }
  html, body { width: 990px; height: 1200px; overflow: hidden; background: var(--page-bg); }
  .flyer {
    position: absolute; left: 31px; top: 0; width: 927px; height: 1200px;
    overflow: hidden; background: var(--night);
    font-family: "Montserrat", sans-serif; color: var(--white);
  }
  .bokeh-field {
    position: absolute; inset: 0;
    background:
      radial-gradient(ellipse 70% 30% at 50% 78%, rgba(236,170,30,.85), rgba(180,110,10,.45) 55%, transparent 80%),
      linear-gradient(180deg, #120709 0%, #17090a 40%, #4a2c06 62%, #8b5c0e 80%, #3a2306 100%);
  }
  .emblem-art {
    position: absolute; left: 255px; top: 58px; width: 417px; height: 404px;
    border-radius: 12px;
    background: radial-gradient(ellipse at center, #3a2610 0%, #22140a 60%, #170c08 100%);
  }
  .anniversary-heading {
    position: absolute; left: 255px; top: 58px; width: 417px; height: 404px;
    display: flex; flex-direction: column; align-items: center; text-align: center;
    font-family: "Tinos", serif; font-weight: 700;
  }
  .anniversary-heading .celebrate { margin-top: 30px; font-size: 30px; letter-spacing: 3px; color: var(--white); }
  .anniversary-heading .year-number { margin-top: 6px; font-size: 170px; line-height: 1; color: var(--gold); }
  .anniversary-heading .year-word { margin-top: 4px; font-size: 38px; line-height: 1; color: var(--gold); }
  .anniversary-heading .anniversary-word {
    margin-top: 16px; font-family: "Montserrat", sans-serif; font-weight: 600;
    font-size: 24px; letter-spacing: 1px; color: var(--gold-light);
  }

  .lead-in {
    position: absolute; top: 467px; width: 100%; text-align: center;
    font-family: "Tinos", serif; font-style: italic; font-weight: 700; font-size: 34px;
    text-shadow: 2px 2px 0 #000;
  }
  .promo-title {
    position: absolute; top: 515px; width: 100%; text-align: center;
    font-family: "Tinos", serif; font-weight: 700; font-size: 51px; letter-spacing: .5px;
    text-shadow: 3px 3px 0 #000;
  }
  .headline {
    position: absolute; top: 590px; width: 100%; text-align: center;
    font-family: "Anton", sans-serif; font-size: 146px; line-height: 1.1; letter-spacing: 2px;
    background: linear-gradient(180deg, var(--gold-light) 0%, var(--gold) 45%, #b57e12 70%, var(--gold-light) 100%);
    -webkit-background-clip: text; background-clip: text; color: transparent;
    -webkit-text-stroke: 3px var(--white);
    filter: drop-shadow(5px 5px 0 rgba(0,0,0,.75));
  }
  .offer-bar {
    position: absolute; left: 98px; top: 766px; width: 731px; height: 50px;
    background: var(--orange); text-align: center; line-height: 50px;
    font-weight: 700; font-size: 21px;
  }
  .offer-frame {
    position: absolute; left: 98px; top: 816px; width: 731px; height: 87px;
    border: 2px solid var(--orange); border-top: none;
  }
  .valid-dates {
    position: absolute; left: 187px; top: 826px; width: 553px; height: 50px;
    background: #120a06; text-align: center; line-height: 50px;
    font-weight: 700; font-size: 36px; letter-spacing: .5px;
  }
  .valid-dates .dates { color: var(--orange); }
  .supply-note {
    position: absolute; left: 313px; top: 884px; width: 301px; height: 38px;
    background: #120a06; text-align: center; line-height: 38px;
    font-weight: 700; font-size: 22px;
  }
  .footer-curve { position: absolute; left: 0; top: 940px; width: 927px; height: 160px; }
  .brand {
    position: absolute; top: 990px; width: 100%;
    display: flex; justify-content: center; align-items: center; gap: 14px;
  }
  .brand-mark { width: 34px; height: 34px; background: var(--blue); }
  .brand-name { font-weight: 700; font-size: 44px; color: var(--ink); letter-spacing: 1px; }
  .brand-tagline {
    position: absolute; top: 1050px; left: 480px;
    font-size: 8px; font-weight: 600; color: #555; letter-spacing: .5px;
  }
  .contact-band { position: absolute; left: 0; top: 1094px; width: 927px; height: 106px; background: var(--blue); }
  .contact-bar {
    position: absolute; left: 99px; top: 1071px; width: 729px; height: 46px;
    background: var(--orange); text-align: center; line-height: 46px;
    font-weight: 700; font-size: 18px; letter-spacing: .5px;
  }
  .contact-row {
    position: absolute; top: 1134px; width: 100%;
    display: flex; justify-content: center; align-items: center; gap: 18px;
    font-weight: 600; font-size: 18px;
  }
  .contact-item { display: flex; align-items: center; gap: 7px; }
  .contact-item svg { width: 16px; height: 16px; stroke: var(--white); fill: none; stroke-width: 1.5; }
  .divider { width: 2px; height: 22px; background: var(--orange); }
</style>
</head>
<body>
<main class="flyer">
  <div class="bokeh-field" role="img" aria-label="Dark background with glowing gold bokeh lights and sparkles"></div>

  <div class="emblem-art" role="img" aria-label="Gold laurel wreath anniversary emblem with red ribbon"></div>
  <div class="anniversary-heading">
    <p class="celebrate">WE ARE CELEBRATING OUR</p>
    <p class="year-number">1</p>
    <p class="year-word">YEAR</p>
    <p class="anniversary-word">ANNIVERSARY</p>
  </div>

  <p class="lead-in">by offering a</p>
  <h1 class="promo-title">Special Peak-Season Promotion!</h1>
  <h2 class="headline">30 DAYS FREE!</h2>

  <div class="offer-bar">FREE RENTALS for 30 days with a minimum 30-Day rental!</div>
  <div class="offer-frame"></div>
  <div class="valid-dates">VALID FROM <span class="dates">SEP. 1 - DEC. 31</span></div>
  <div class="supply-note">WHILE SUPPLIES LAST.</div>

  <svg class="footer-curve" viewBox="0 0 927 160" preserveAspectRatio="none" aria-hidden="true">
    <path d="M 0 58 Q 463 -10 927 58 L 927 160 L 0 160 Z" fill="#ffffff"/>
  </svg>

  <div class="brand">
    <span class="brand-mark"></span>
    <span class="brand-name">Brakko Leasing</span>
  </div>
  <div class="brand-tagline">BRAKKO-LEASING.EXAMPLE &nbsp;|&nbsp; BY NORVALE</div>

  <div class="contact-band"></div>
  <div class="contact-bar">PLEASE CONTACT OUR SALES DEPARTMENT FOR MORE DETAILS.</div>

  <div class="contact-row">
    <span class="contact-item">
      <svg viewBox="0 0 16 16" aria-hidden="true"><rect x="1.5" y="3.5" width="13" height="9"/><path d="M1.5 3.5 L8 9 L14.5 3.5"/></svg>
      quotes@brakko-leasing.example
    </span>
    <span class="divider"></span>
    <span class="contact-item">
      <svg viewBox="0 0 16 16" aria-hidden="true"><circle cx="8" cy="8" r="7"/><path d="M5.5 4.5 L7 6.5 L6.2 7.5 Q7 9 8.5 9.8 L9.5 9 L11.5 10.5 L10.5 11.8 Q6 11 4.2 5.5 Z"/></svg>
      +1-555-284-9317
    </span>
    <span class="divider"></span>
    <span class="contact-item">
      <svg viewBox="0 0 16 16" aria-hidden="true"><circle cx="8" cy="8" r="7"/><ellipse cx="8" cy="8" rx="3" ry="7"/><path d="M1 8 H15"/></svg>
      brakko-leasing.example
    </span>
  </div>
</main>
</body>
</html>
```